Design a New Business Card for Our Company

We are looking for fresh, unique, and a modern business card that reflects our roots as digital marketing agency focused on SEM.

Industry/Entity Type

Marketing

Contact Information for Business Card

looking for very unique out of the box designs. clean and modern that compliments our logo

Requirements
Must have
• colors should match our logo
• Front should have name, address, email, and phone/fax of the person, phone/fax are the same number
• back should have our url

```html
<!DOCTYPE html>
<html lang="en">
<head>
<meta charset="utf-8">
<title>Brightpath Digital – Business Card</title>
<link rel="stylesheet" href="https://fonts.googleapis.com/css2?family=Source+Sans+3:wght@400;600;700&display=swap">
<style>
  :root {
    --page-bg: #2b2d31;
    --card-white: #ffffff;
    --brand-blue: #5b95d1;
    --text-light: #ffffff;
  }
  * { box-sizing: border-box; margin: 0; padding: 0; }
  html, body {
    width: 1200px;
    height: 864px;
    overflow: hidden;
  }
  body {
    background: var(--page-bg);
    font-family: "Source Sans 3", "Myriad Pro", Arial, sans-serif;
    position: relative;
  }
  .card {
    position: absolute;
    width: 560px;
    height: 320px;
    border-radius: 2px;
    box-shadow: 0 10px 30px rgba(0, 0, 0, 0.35);
    overflow: hidden;
  }

  /* Logo side */
  .card--logo {
    left: 150px;
    top: 70px;
    background: var(--card-white);
  }
  .brand {
    position: absolute;
    left: 0;
    right: 0;
    top: 42px;
    display: flex;
    flex-direction: column;
    align-items: center;
  }
  .brand__dot {
    width: 58px;
    height: 58px;
    border-radius: 50%;
    background: var(--brand-blue);
    margin-bottom: 14px;
  }
  .brand__name {
    font-size: 44px;
    font-weight: 700;
    color: var(--brand-blue);
    letter-spacing: -0.5px;
    line-height: 1;
  }
  .url-band {
    position: absolute;
    left: 0;
    right: 0;
    top: 212px;
    height: 40px;
    background: var(--brand-blue);
    display: flex;
    align-items: center;
    justify-content: center;
  }
  .url-band__url {
    color: var(--text-light);
    font-size: 15px;
    font-weight: 700;
    letter-spacing: 0.3px;
  }

  /* Contact side */
  .card--contact {
    left: 500px;
    top: 470px;
    background: var(--brand-blue);
    color: var(--text-light);
    text-align: center;
  }
  .person {
    position: absolute;
    left: 0;
    right: 0;
    top: 62px;
  }
  .person__name {
    font-size: 22px;
    font-weight: 700;
    line-height: 1.1;
  }
  .person__role {
    font-size: 15px;
    font-weight: 400;
    margin-top: 2px;
  }
  .contact {
    position: absolute;
    left: 0;
    right: 0;
    top: 150px;
    font-size: 16px;
    line-height: 1.38;
  }
  .contact__address {
    margin-top: 12px;
  }
</style>
</head>
<body>

  <section class="card card--logo" aria-label="Business card, logo side">
    <div class="brand">
      <span class="brand__dot" aria-hidden="true"></span>
      <span class="brand__name">Brightpath Digital</span>
    </div>
    <div class="url-band">
      <span class="url-band__url">www.brightpathdigital.com</span>
    </div>
  </section>

  <section class="card card--contact" aria-label="Business card, contact side">
    <div class="person">
      <p class="person__name">Daniel Reeves</p>
      <p class="person__role">Managing Director</p>
    </div>
    <div class="contact">
      <p class="contact__phone">(021)-738-4152</p>
      <p class="contact__phone">487-209-6613</p>
      <p class="contact__email">daniel@brightpath.co</p>
      <p class="contact__address">48 Harlow Street, Millbrook Bay, Westland 60417</p>
    </div>
  </section>

</body>
</html>
```